We are a new company with 2 divisions a medical research and medical product sales. We need a company logo and Business Cards. The design files need to be provided to us in Adobe Photoshop CS 5.1.

Target Market(s)

Medical Community

Industry/Entity Type

Medical

Contact Information for Business Card

Company Name - Harrowgate Lifesciences LLC
Company Address 4127 Larkspur Ave Suite 7, Gainesville Fl 32614

Requirements
Must have
• The design files need to be provided to us in Adobe Photoshop CS 5.1.

```html
<!DOCTYPE html>
<html lang="en">
<head>
<meta charset="utf-8">
<title>Harrowgate Lifesciences LLC – Business Card</title>
<link rel="stylesheet" href="https://fonts.googleapis.com/css2?family=Lato:wght@400;700&display=swap">
<style>
  :root {
    --backdrop: #161616;
    --card: #2a2a2b;
    --ink: #f2f2f2;
    --accent: #3d8cc9;
    --rule: #8a8a8a;
  }
  * { box-sizing: border-box; margin: 0; padding: 0; }
  html, body {
    width: 1200px; height: 900px; overflow: hidden;
    background: var(--backdrop);
    font-family: "Lato", Arial, sans-serif;
  }
  .card {
    position: absolute;
    left: 100px; top: 165px;
    width: 1000px; height: 570px;
    background: var(--card);
    border-radius: 28px;
    color: var(--ink);
  }
  .brand {
    position: absolute;
    left: 60px; top: 250px;
    width: 380px;
    display: flex; align-items: center; gap: 14px;
  }
  .brand-dot {
    flex: none;
    width: 22px; height: 22px; border-radius: 50%;
    background: var(--accent);
  }
  .brand-name {
    font-weight: 400; font-size: 27px; letter-spacing: 0.5px;
    color: var(--ink); line-height: 1.25;
  }
  .person {
    position: absolute; right: 100px; top: 205px;
    text-align: right;
  }
  .person-name { font-size: 28px; font-weight: 400; }
  .person-title { font-size: 19px; color: var(--accent); margin-top: 8px; }
  .divider {
    position: absolute; left: 436px; right: 100px; top: 303px;
    height: 1px; background: var(--rule);
  }
  .contact {
    position: absolute; right: 100px; top: 340px;
    text-align: right; font-size: 19px; line-height: 1.35;
  }
  .address { margin-bottom: 24px; margin-right: 0; }
  .contact-line {
    display: flex; justify-content: flex-end; align-items: center;
    gap: 12px; height: 32px;
  }
  .contact-line svg { width: 20px; height: 20px; fill: var(--accent); flex: none; }
</style>
</head>
<body>
  <main class="card">
    <div class="brand">
      <span class="brand-dot"></span>
      <span class="brand-name">HARROWGATE LIFESCIENCES LLC</span>
    </div>

    <div class="person">
      <p class="person-name">Name of the Person</p>
      <p class="person-title">Managing Director</p>
    </div>

    <div class="divider"></div>

    <div class="contact">
      <p class="address">4127 Larkspur Ave Suite 7,<br>Gainesville Fl 32614</p>
      <p class="contact-line">044 1235 67890
        <svg viewBox="0 0 20 20" aria-hidden="true"><path d="M3 7c0-2 3-3 7-3s7 1 7 3v1h-4V6.5c-2-.6-4-.6-6 0V8H3z"/><path d="M6 9h8l3 6v2H3v-2z"/></svg>
      </p>
      <p class="contact-line">info@harrowgatelifesciences.com
        <svg viewBox="0 0 20 20" aria-hidden="true"><path d="M2 4h16v12H2z" fill="var(--accent)"/><path d="M2.5 4.5l7.5 6 7.5-6" stroke="var(--card)" stroke-width="1.4" fill="none"/></svg>
      </p>
      <p class="contact-line">www.harrowgatelifesciences.com
        <svg viewBox="0 0 20 20" aria-hidden="true" style="fill:none;stroke:var(--accent);stroke-width:2"><path d="M8 12l4-4"/><path d="M9 6l2-2a3 3 0 014 4l-2 2"/><path d="M11 14l-2 2a3 3 0 01-4-4l2-2"/></svg>
      </p>
    </div>
  </main>
</body>
</html>
```